We would like a Industrial brouchure design, for OIL and Gas and chemical industry , target customers are Petrochemical refineries, power plants and Petroleum tanker trucks.
this brouchure should have product photos of our main products.
I.E - stainless steel expasnion joints, rubber expansion joints, Fabric expansion joints, Composite hose, hand built rubber hose.
this brouchure is to hand to customers to show them our company capabilities
Design ideas can be taken from our web site - www.dorvenic.com.au
Our products are high end engineered products, we supply all of Australia, new Zealand and south east asia and pacific islands
i would like a location map on the brouchure showing our locations.
our locations are -

Perth Western Australia
Port hedland western Australia
Darwin Northen territory
Adelaide - south Australia
Brisbane - Queensland - Australia
Auckland - New zealnd
Singapore
Surabaya - Indonesia
jakarta - indonesia
Ho Chi Min City - Vietnam
balikpapan - indonesia

our comapny logo colors are Black and grey

we would need product photos as well for the following products

Composite hose
stainless steel expansion joints
rubber expasnion joints
Fabric expansion joints
hand biuilt rubber hose
Composite ship to shore petroleum dock hose
stainless braided flexible hose

Target Market(s)

petrochemical industry
refineries, petroleum tanker, power plants, mining

Requirements
Must have
• product photos
• map of where we are located
• high end company impression
Nice to have
• 3 plus pages

```html
<!DOCTYPE html>
<html lang="en">
<head>
<meta charset="utf-8">
<title>Dorvenic – Our Products Spread</title>
<link href="https://fonts.googleapis.com/css2?family=Michroma&family=Open+Sans:ital,wght@0,400;0,600;1,800&display=swap" rel="stylesheet">
<style>
  :root {
    --backdrop: #262626;
    --paper: #f4f4f4;
    --panel: rgba(24, 24, 24, 0.9);
    --panel-solid: #1c1c1c;
    --ink: #2b2b2b;
    --ink-soft: #4a4a4a;
    --on-dark: #f2f2f2;
    --on-dark-soft: #cfcfcf;
    --rule-dark: #333333;
  }
  * { box-sizing: border-box; margin: 0; padding: 0; }
  html, body { width: 1200px; height: 833px; overflow: hidden; background: var(--backdrop); }
  .canvas { position: relative; width: 1200px; height: 833px; }

  .spread {
    position: absolute; left: 50px; top: 28px;
    width: 1100px; height: 777px; display: flex;
    box-shadow: 0 18px 40px rgba(0,0,0,.55);
  }
  .page { position: relative; width: 550px; height: 777px; background: var(--paper); overflow: hidden; }
  .page--left::after, .page--right::before {
    content: ""; position: absolute; top: 0; bottom: 0; width: 40px; pointer-events: none; z-index: 5;
  }
  .page--left::after { right: 0; background: linear-gradient(90deg, transparent, rgba(0,0,0,.18)); }
  .page--right::before { left: 0; background: linear-gradient(270deg, transparent, rgba(0,0,0,.16)); }

  .photo { position: absolute; }

  .heading {
    font-family: "Michroma", sans-serif; font-weight: 400; letter-spacing: .04em; line-height: 1.25;
  }
  .heading::after {
    content: ""; display: block; width: 34px; height: 2px; margin-top: 7px; background: currentColor;
  }
  .body-copy {
    font-family: "Open Sans", sans-serif; font-size: 7.4px; line-height: 1.5; margin-top: 7px;
  }
  .body-copy + .body-copy { margin-top: 5px; }

  /* Left page */
  .photo--refinery {
    left: 0; top: 0; width: 550px; height: 430px;
    background: linear-gradient(180deg, #8a8fa6 0%, #c9a36c 30%, #b07a3e 50%, #5b4a3a 72%, #2d2a28 100%);
  }
  .section-tab {
    position: absolute; left: 150px; top: 0; width: 200px; height: 52px; background: var(--panel-solid);
    display: flex; align-items: center; justify-content: center;
    font-family: "Open Sans", sans-serif; font-style: italic; font-weight: 800; font-size: 17px;
    letter-spacing: .06em; color: var(--on-dark);
  }
  .intro { position: absolute; left: 140px; top: 68px; width: 360px; color: var(--ink); }
  .intro .heading { font-size: 16px; }
  .intro .heading::after { display: none; }
  .intro .body-copy { margin-top: 6px; color: #1e1e1e; }

  .panel--left {
    position: absolute; left: 0; top: 390px; width: 360px; height: 330px; background: var(--panel);
    padding: 34px 62px 0 40px; color: var(--on-dark);
  }
  .panel--left .heading { font-size: 13px; }
  .panel--left .body-copy { color: var(--on-dark-soft); }
  .panel--left .block + .block { margin-top: 22px; }

  .photo--pump {
    left: 340px; top: 410px; width: 210px; height: 150px;
    background: linear-gradient(135deg, #d9dde2 0%, #9aa3ad 45%, #2f5fae 60%, #c4c9cf 100%);
  }
  .photo--manifold {
    left: 320px; top: 560px; width: 230px; height: 190px;
    background: linear-gradient(160deg, #c8ccd1 0%, #7b828a 40%, #c0622e 62%, #3b3f44 100%);
  }

  /* Right page */
  .photo--reflection {
    left: 0; top: 0; width: 550px; height: 460px;
    background: linear-gradient(180deg, #55575c 0%, #8a7f6e 45%, #c4a878 70%, #e8e8e8 100%);
  }
  .photo--nozzle {
    left: 400px; top: 0; width: 150px; height: 430px;
    background: linear-gradient(170deg, #e9e9e9 0%, #cfcfcf 30%, #d13a37 48%, #8f1f22 60%, #5c5b5d 100%);
  }
  .panel--right {
    position: absolute; left: 0; top: 0; width: 400px; height: 400px; background: var(--panel);
    padding: 80px 40px 0 70px; color: var(--on-dark);
  }
  .panel--right .heading { font-size: 13px; }
  .panel--right .body-copy { color: var(--on-dark-soft); }
  .panel--right .block + .block { margin-top: 22px; }

  .lower-copy { position: absolute; left: 70px; top: 470px; width: 285px; color: var(--ink); }
  .lower-copy .heading { font-size: 13px; color: var(--ink); }
  .lower-copy .heading::after { background: var(--rule-dark); }
  .lower-copy .body-copy { color: var(--ink-soft); }
  .lower-copy .block + .block { margin-top: 22px; }

  .photo--pipework {
    left: 380px; top: 450px; width: 170px; height: 150px;
    background: linear-gradient(150deg, #2f8f3a 0%, #4cc04e 35%, #a9aaa4 60%, #7d7c76 100%);
  }
  .photo--drums {
    left: 370px; top: 600px; width: 180px; height: 150px;
    background: linear-gradient(180deg, #7fb3df 0%, #9fc4e2 30%, #1d49c9 55%, #0f2a8a 80%, #9a9a9a 100%);
  }
</style>
</head>
<body>
<main class="canvas">
  <div class="spread">

    <section class="page page--left">
      <div class="photo photo--refinery" role="img" aria-label="Petrochemical refinery towers at sunset with a tanker ship moored alongside"></div>
      <div class="section-tab">OUR PRODUCTS</div>

      <div class="intro">
        <h2 class="heading">Fluid Transfer Solutions</h2>
        <p class="body-copy">Dorvenic has extensive industry experience, which allows us to provide highly professional services and the best quality products. Our wide range of fluid transfer services will help with all of your business needs and our products comply with all relevant safety and quality standards.</p>
      </div>

      <div class="panel--left">
        <div class="block">
          <h3 class="heading">Composite Hoses and Assemblies</h3>
          <p class="body-copy">Our complete Composite hose range includes a wide selection of hoses that cater for the Petroleum/Oil &amp; Chemical industries. We also stock a comprehensive range of fitting for these industries in materials such as Steel, Stainless, and Polypropylene. Our Hose &amp; Fittings comply with all the relevant Australian and International standards.</p>
        </div>
        <div class="block">
          <h3 class="heading">Metallic Hose &amp; Assemblies</h3>
          <p class="body-copy">Our quality Stainless Steel braided hoses can be assembled with almost any connection. The pressure and chemical compatibility of these products make them suitable for a wide range of uses in almost any industry. The hose assemblies are available in Stainless Steel 304, 316 and 321 on request. The hoses are manufactured, assembled and tested in accordance with the relevant ISO 10380 standard.</p>
        </div>
      </div>

      <div class="photo photo--pump" role="img" aria-label="Blue industrial pump with stainless steel pipework and valves"></div>
      <div class="photo photo--manifold" role="img" aria-label="Row of hose assemblies with orange fittings connected to a manifold"></div>
    </section>

    <section class="page page--right">
      <div class="photo photo--reflection" role="img" aria-label="Refinery lights reflected on calm water at dusk"></div>
      <div class="photo photo--nozzle" role="img" aria-label="Hand holding a red fuel nozzle at a tanker filling point"></div>

      <div class="panel--right">
        <div class="block">
          <h3 class="heading">Custom Fabrication and Testing Services</h3>
          <p class="body-copy">Our fully functional workshop is able to design, customise, and fabricate a wide range of fluid transfer products. This goes hand in hand with our in-house and on-site testing facilities.</p>
          <p class="body-copy">Whether it is one hose or a full fleet of fuel tankers, we are able to handle your testing and certification requirements to meet Australian and international standards.</p>
        </div>
        <div class="block">
          <h3 class="heading">Rubber Expansion Joints</h3>
          <p class="body-copy">Dorvenic supplies standard and custom sized fabricated rubber joints made from a large range of materials. We are able to supply single and twin sphere rubber joints in both EPDM and NBR off the shelf with either plated steel or stainless steel flanges.</p>
          <p class="body-copy">We hold Table D/E, ANSI 150, and DIN flanges in stock and have the ability to supply alternate flanges with a quick turn around. Control rods and vacuum rings are also readily available.</p>
        </div>
      </div>

      <div class="lower-copy">
        <div class="block">
          <h3 class="heading">Fluid Transfer Fittings &amp; Accessories</h3>
          <p class="body-copy">We stock a range of fittings and accessories to suit many industries. Specialising but not limited to product such as PVC spiral guard, Bitumen fittings, Thermal sleeve, Plugs and caps, Hose buns, Dry break couplings, Custom test tags and all associated industry fittings in a variety of materials.</p>
        </div>
        <div class="block">
          <h3 class="heading">Fabric and Metal Expansion Joints</h3>
          <p class="body-copy">We have quality fabric and metallic expansion joints designed and manufactured to suit specific customer requirements. Each expansion joint is reviewed by trained technical staff and a quote provided for your approval.</p>
          <p class="body-copy">Our technical experience and engineering support can help you determine which product will best suit your needs.</p>
        </div>
      </div>

      <div class="photo photo--pipework" role="img" aria-label="Metallic expansion joint installed between green painted pipework"></div>
      <div class="photo photo--drums" role="img" aria-label="Blue chemical drums stacked on pallets at a port with cranes behind"></div>
    </section>

  </div>
</main>
</body>
</html>
```